Veldmark Supplies Business Card

Professional business card that stand out to our potential customers. Front and back with clean modern design

Industry/Entity Type

Oil and gas

Contact Information for Business Card

Name, address, website , office phone and cell number

Requirements
Must have
• Editable files for each employee

```html
<!DOCTYPE html>
<html lang="en">
<head>
<meta charset="UTF-8">
<title>Veldmark Supplies Business Card</title>
<link href="https://fonts.googleapis.com/css2?family=Poppins:wght@400;500;700;800&display=swap" rel="stylesheet">
<style>
  :root {
    --stage: #2b2b2d;
    --card-dark: #1e1e1f;
    --card-light: #f7f7f7;
    --brand-red: #e8202a;
    --brand-blue: #13a9cc;
    --ink: #1b1b1b;
    --rule: #555555;
  }
  * { margin: 0; padding: 0; box-sizing: border-box; }
  html, body {
    width: 1200px; height: 900px; overflow: hidden;
    background: var(--stage);
    font-family: "Poppins", sans-serif;
  }
  .stage {
    width: 1200px; height: 900px;
    display: flex; flex-direction: column;
    align-items: center; justify-content: center; gap: 56px;
  }
  .card {
    width: 560px; height: 320px;
    border-radius: 18px; position: relative; overflow: hidden;
  }
  /* Back */
  .card-back {
    background: var(--card-dark);
    display: flex; align-items: center; justify-content: center;
  }
  .brand-name {
    display: flex; align-items: center; gap: 14px;
    font-weight: 800; text-transform: uppercase; letter-spacing: 1px;
    color: var(--brand-red);
  }
  .brand-mark { width: 26px; height: 26px; background: var(--brand-red); }
  .card-back .brand-name { font-size: 38px; }
  .card-back .brand-mark { width: 34px; height: 34px; }
  /* Front */
  .card-front { background: var(--card-light); }
  .front-brand {
    position: absolute; left: 34px; top: 118px; width: 210px;
  }
  .front-brand .brand-name { font-size: 22px; gap: 10px; }
  .front-brand .brand-mark { width: 20px; height: 20px; }
  .divider {
    position: absolute; left: 262px; top: 70px; width: 1px; height: 170px;
    background: var(--rule);
  }
  .contact {
    position: absolute; left: 284px; top: 66px; color: var(--ink);
  }
  .contact-name { font-size: 25px; font-weight: 700; color: var(--brand-red); line-height: 1.1; }
  .contact-role { font-size: 14px; font-weight: 500; margin-bottom: 8px; }
  .contact-address { font-size: 13px; line-height: 1.35; margin-bottom: 6px; }
  .contact-list { list-style: none; font-size: 13px; line-height: 1.5; }
  .contact-list li { display: flex; align-items: center; gap: 8px; }
  .contact-list svg { width: 11px; height: 11px; fill: var(--brand-red); flex: none; }
  .footer-bands {
    position: absolute; left: 0; bottom: 0; width: 100%; height: 16px;
  }
</style>
</head>
<body>
<main class="stage">
  <section class="card card-back" aria-label="Card back">
    <div class="brand-name"><span class="brand-mark"></span>Veldmark Supplies</div>
  </section>

  <section class="card card-front" aria-label="Card front">
    <div class="front-brand">
      <div class="brand-name"><span class="brand-mark"></span>Veldmark Supplies</div>
    </div>
    <div class="divider"></div>
    <div class="contact">
      <p class="contact-name">Colin Marsh</p>
      <p class="contact-role">President</p>
      <p class="contact-address">417 N.Harlow Ave Suite 5<br>Midland, Tx 79701</p>
      <ul class="contact-list">
        <li><svg viewBox="0 0 24 24"><path d="M6.6 10.8a15.1 15.1 0 0 0 6.6 6.6l2.2-2.2c.3-.3.7-.4 1-.2 1.1.4 2.3.6 3.6.6.6 0 1 .4 1 1V20c0 .6-.4 1-1 1C10.6 21 3 13.4 3 4c0-.6.4-1 1-1h3.5c.6 0 1 .4 1 1 0 1.3.2 2.5.6 3.6.1.3 0 .7-.2 1z"/></svg>(555)204-3817</li>
        <li><svg viewBox="0 0 24 24"><path d="M7 1h10a2 2 0 0 1 2 2v18a2 2 0 0 1-2 2H7a2 2 0 0 1-2-2V3a2 2 0 0 1 2-2zm0 3v14h10V4zm5 15.5a1 1 0 1 0 0 2 1 1 0 0 0 0-2z"/></svg>(555)204-3817</li>
        <li><svg viewBox="0 0 24 24"><path d="M2 5h20v14H2zm2 2v.5l8 5 8-5V7z"/></svg>sales@veldmarksupplies.com</li>
        <li><svg viewBox="0 0 24 24"><circle cx="12" cy="12" r="10"/></svg>www.veldmarksupplies.com</li>
      </ul>
    </div>
    <svg class="footer-bands" viewBox="0 0 560 16" preserveAspectRatio="none">
      <polygon points="0,0 250,0 238,16 0,16" fill="var(--brand-red)"/>
      <polygon points="256,0 560,0 560,16 244,16" fill="var(--brand-blue)"/>
    </svg>
  </section>
</main>
</body>
</html>
```